Industry / Entity Type

Financial consultancy / advisers

Current site is: http://www.brightmoor-counsel.com

Looking for a complete overhaul of this site, we are after a clean modern look. Will require the ability to easily add, update and remove content, hence the WordPress design.
Example:
Add case studies
Industry documentation (downloadable brochures / flyers and such)

What we like from our current site is the colour the fonts and the logo (the city of London) we would like to have other city outlines (NYC and Tokyo, Hong Kong, Singapore).

The site will be used by our potential clients to get in contact and re-view the case studies, if possible would like to have a client login area where they can download our documents like NDA’s etc and T&C’s.

Task Outline

Create a Web Design (Coded - Design and coding required)
Designer must provide full implementation/coding depending on the platform chosen by the client (i.e. WordPress theme, HTML/CSS, bootstrap etc.)

Task Description

I need a full website built that must work on desktop and mobile. I can provide the London city skyline and the font file, which we have used. Some stock industrial photos will be required.

Requirements:

*Splash page
*What We Do
*How We do it
*Who Are We? To have the same information and links as the current site
*Why use us?
*Clients: To have the same information and links as the current site
*Partners: To have the same information and links as the current site
*Contact:

Target Market(s)

Financial institutions trading Equities, Futures, Options, Forex and Fixed Income.
Regulators, Exchanges, ECN’s
Buy side firms and Sell side firms

Industry/Entity Type

Financial

Coding

Coded - Design and coding required

Number of Pages Required

5+ page

Font styles to use
Sans Serif

Colors
f04a50

Requirements
Must have
• Splash page
• What We Do
• How We do it
• Who Are We? To have the same information and links as the current site
• Why use us?
• Clients: To have the same information and links as the current site
• Partners: To have the same information and links as the current site
• Contact:

```html
<!DOCTYPE html>
<html lang="en">
<head>
<meta charset="utf-8">
<title>Brightmoor Counsel</title>
<link href="https://fonts.googleapis.com/css2?family=Open+Sans:wght@400;600;700&display=swap" rel="stylesheet">
<style>
:root{
  --red:#f04a50;
  --ink:#333;
  --muted:#8a8a8a;
  --grey-bg:#f1f1f1;
  --line:#dcdcdc;
  --footer:#2b2b2b;
  --footer-deep:#1d1d1d;
  --white:#fff;
}
*{box-sizing:border-box;margin:0;padding:0}
html,body{width:1200px;height:2972px;overflow:hidden}
body{font-family:"Open Sans",Arial,sans-serif;color:var(--ink);background:var(--white);font-size:13px;line-height:1.6}
.container{width:980px;margin:0 auto;position:relative}
.brand{height:120px;display:flex;align-items:center;justify-content:center;gap:12px}
.brand-mark{width:22px;height:22px;background:var(--ink)}
.brand-name{font-size:22px;font-weight:600;letter-spacing:4px;color:var(--ink)}
.main-nav{height:40px;border-top:1px solid var(--line)}
.main-nav ul{list-style:none;display:flex;justify-content:center;height:40px}
.main-nav li{padding:0 20px;font-size:12px;font-weight:600;line-height:40px;color:#555;text-transform:uppercase}
.main-nav li.active{background:var(--red);color:var(--white)}
.hero{height:460px;position:relative;background:linear-gradient(180deg,#9fb8cf 0%,#c9d6e0 35%,#8a8c8f 70%,#5d5a55 100%)}
.hero-label{position:absolute;right:60px;top:190px;text-align:right}
.hero-label span{display:inline-block;background:var(--red);color:var(--white);font-size:26px;letter-spacing:2px;padding:6px 18px;margin-top:4px;text-transform:uppercase}
.hero-arrow{position:absolute;top:210px;width:40px;height:40px;border-radius:50%;background:rgba(0,0,0,.45)}
.hero-arrow.prev{left:16px}.hero-arrow.next{right:16px}
.hero-arrow svg{width:40px;height:40px}
.section-title{font-size:26px;font-weight:700;text-transform:uppercase;color:var(--ink);padding-bottom:14px;border-bottom:1px solid var(--line);position:relative;margin-bottom:44px}
.section-title::after{content:"";position:absolute;left:0;bottom:-2px;width:60px;height:3px;background:var(--red)}
.services{height:600px;padding-top:50px}
.service-grid{display:grid;grid-template-columns:repeat(4,1fr);gap:60px 40px}
.service svg{width:44px;height:44px;stroke:var(--red);fill:none;stroke-width:2}
.service h3{color:var(--red);font-size:14px;font-weight:600;margin:12px 0 6px;text-transform:uppercase}
.service p{color:var(--muted);font-size:12px}
.about{height:400px;background:var(--grey-bg);padding-top:50px}
.about-text{width:440px}
.about-text p{color:var(--muted);font-size:12px;margin-bottom:20px}
.btn{display:inline-block;background:var(--red);color:var(--white);font-size:11px;font-weight:600;text-transform:uppercase;padding:6px 14px}
.about-photo{position:absolute;right:-60px;top:-20px;width:560px;height:330px;background:linear-gradient(135deg,#e9ecef,#b7c2cc 55%,#6f7b86)}
.team{height:510px;padding-top:50px}
.team-grid{display:grid;grid-template-columns:repeat(4,1fr);gap:40px}
.member{text-align:left}
.member-photo{width:130px;height:130px;border-radius:50%;margin:0 auto 20px;background:radial-gradient(circle,#d6c1ad,#8a7565)}
.member h3{color:var(--red);font-size:14px;font-weight:600;text-transform:uppercase}
.member p{color:var(--muted);font-size:12px;margin:6px 0 14px}
.news{height:530px;background:var(--grey-bg);padding-top:50px}
.news-grid{display:grid;grid-template-columns:repeat(3,1fr);gap:40px}
.news-photo{height:160px;position:relative;background:linear-gradient(135deg,#cfd6dc,#8c98a3)}
.news-date{position:absolute;left:14px;top:14px;width:50px;background:var(--red);color:var(--white);text-align:center;font-size:11px;font-weight:700;line-height:1.3;padding:4px 0}
.news-date b{display:block;font-size:18px}
.news-item h3{color:var(--red);font-size:14px;font-weight:600;margin:16px 0 8px;text-transform:uppercase}
.news-item p{color:var(--muted);font-size:12px;margin-bottom:14px}
.site-footer{height:280px;background:var(--footer);color:#bbb;padding-top:40px}
.footer-grid{display:grid;grid-template-columns:1.4fr 1fr 1fr 1.3fr 1fr;gap:30px}
.footer-grid h4{color:var(--white);font-size:12px;font-weight:700;text-transform:uppercase;margin-bottom:12px}
.footer-grid p,.footer-grid li{font-size:11px;list-style:none;line-height:1.8}
.social{display:flex;gap:8px}
.social span{width:24px;height:24px;border-radius:50%;border:1px solid #888}
.copyright{height:32px;background:var(--footer-deep);color:#888;font-size:11px;text-align:center;line-height:32px}
</style>
</head>
<body>
<header>
  <div class="brand"><span class="brand-mark"></span><span class="brand-name">BRIGHTMOOR COUNSEL</span></div>
  <nav class="main-nav"><ul>
    <li class="active">Home</li><li>What We Do</li><li>How We Do It</li><li>Who Are We</li><li>Why Use Us</li><li>Clients</li><li>Partners</li><li>Contact</li>
  </ul></nav>
</header>

<section class="hero" role="img" aria-label="City skyline of glass office towers under a pale sky">
  <div class="hero-label"><span>Brightmoor Counsel</span></div>
  <div class="hero-arrow prev"><svg viewBox="0 0 40 40"><path d="M23 13l-7 7 7 7" stroke="#fff" stroke-width="2" fill="none"/></svg></div>
  <div class="hero-arrow next"><svg viewBox="0 0 40 40"><path d="M17 13l7 7-7 7" stroke="#fff" stroke-width="2" fill="none"/></svg></div>
</section>

<section class="services"><div class="container">
  <h2 class="section-title">What We Do</h2>
  <div class="service-grid">
    <div class="service"><svg viewBox="0 0 44 44"><rect x="8" y="6" width="28" height="32"/><path d="M14 16h16M14 22h16M14 28h10"/></svg><h3>Case Studies</h3><p>We review real client projects and share the results that matter most to them.</p></div>
    <div class="service"><svg viewBox="0 0 44 44"><circle cx="16" cy="16" r="6"/><circle cx="30" cy="18" r="5"/><path d="M5 36c2-8 8-11 11-11s9 3 11 11M26 28c5 0 10 3 12 8"/></svg><h3>Our Clients</h3><p>Banks, brokers and exchanges trust us to guide change across their trading desks.</p></div>
    <div class="service"><svg viewBox="0 0 44 44"><path d="M4 22l8-8 8 4 6-4 14 8M12 26l6 6 4-2 4 4 8-8"/></svg><h3>Partners</h3><p>We work beside leading vendors to deliver tools that fit each client well.</p></div>
    <div class="service"><svg viewBox="0 0 44 44"><circle cx="22" cy="22" r="16"/><path d="M6 22h32M22 6c6 6 6 26 0 32M22 6c-6 6-6 26 0 32"/></svg><h3>Downloads</h3><p>Brochures, flyers and forms are ready for clients to save and read at ease.</p></div>
    <div class="service"><svg viewBox="0 0 44 44"><circle cx="22" cy="14" r="7"/><path d="M8 38c2-9 8-13 14-13s12 4 14 13"/></svg><h3>Management</h3><p>Clear project leadership keeps every team on time, on budget and on track.</p></div>
    <div class="service"><svg viewBox="0 0 44 44"><circle cx="22" cy="22" r="7"/><path d="M22 4v6M22 34v6M4 22h6M34 22h6M9 9l4 4M31 31l4 4M9 35l4-4M31 13l4-4"/></svg><h3>Development</h3><p>We design and build trading systems that scale with growing market demands.</p></div>
    <div class="service"><svg viewBox="0 0 44 44"><rect x="8" y="6" width="22" height="30"/><circle cx="28" cy="28" r="7"/><path d="M33 33l6 6"/></svg><h3>Research</h3><p>Our analysts track rules, markets and new tech so clients stay ahead of them.</p></div>
    <div class="service"><svg viewBox="0 0 44 44"><path d="M22 6a11 11 0 0 0-6 20v5h12v-5a11 11 0 0 0-6-20zM17 36h10"/></svg><h3>Advisors</h3><p>Seasoned experts give honest advice on strategy, risk and vendor selection.</p></div>
  </div>
</div></section>

<section class="about"><div class="container">
  <h2 class="section-title" style="width:440px">About Brightmoor</h2>
  <div class="about-text">
    <p>Since founding, Brightmoor Counsel has helped financial firms plan and deliver change across equities, futures, options, forex and fixed income. We bring years of hands on trading experience to each engagement. Our advisers work closely with buy side and sell side firms, regulators, exchanges and networks to pick the right technology, shape sound processes and build lasting value for every client we serve.</p>
    <span class="btn">Read More</span>
  </div>
  <div class="about-photo" role="img" aria-label="Business team meeting around a laptop in a bright office"></div>
</div></section>

<section class="team"><div class="container">
  <h2 class="section-title">Our Team</h2>
  <div class="team-grid">
    <div class="member"><div class="member-photo" role="img" aria-label="Portrait of Matt Holloway"></div><h3>Matt Holloway</h3><p>Founder with deep roots in trading technology and a focus on client outcomes.</p><span class="btn">Read More</span></div>
    <div class="member"><div class="member-photo" role="img" aria-label="Portrait of Jane Ashcroft"></div><h3>Jane Ashcroft</h3><p>Leads our delivery team and keeps complex programmes moving smoothly forward.</p><span class="btn">Read More</span></div>
    <div class="member"><div class="member-photo" role="img" aria-label="Portrait of Paul Renwick"></div><h3>Paul Renwick</h3><p>Heads research on market rules, venues and new trading platform trends.</p><span class="btn">Read More</span></div>
    <div class="member"><div class="member-photo" role="img" aria-label="Portrait of Mark Ellison"></div><h3>Mark Ellison</h3><p>Senior adviser guiding clients through vendor choice and system design.</p><span class="btn">Read More</span></div>
  </div>
</div></section>

<section class="news"><div class="container">
  <h2 class="section-title">Latest News</h2>
  <div class="news-grid">
    <div class="news-item"><div class="news-photo" role="img" aria-label="Colleagues reviewing documents at a desk"><div class="news-date"><b>01</b>APR</div></div><h3>Market Update News</h3><p>A short summary of recent market changes and what they mean for trading firms this quarter.</p><span class="btn">Read More</span></div>
    <div class="news-item"><div class="news-photo" role="img" aria-label="Team discussion in a meeting room"><div class="news-date"><b>01</b>APR</div></div><h3>Market Update News</h3><p>A short summary of recent market changes and what they mean for trading firms this quarter.</p><span class="btn">Read More</span></div>
    <div class="news-item"><div class="news-photo" role="img" aria-label="Advisers presenting to a client"><div class="news-date"><b>01</b>APR</div></div><h3>Market Update News</h3><p>A short summary of recent market changes and what they mean for trading firms this quarter.</p><span class="btn">Read More</span></div>
  </div>
</div></section>

<footer class="site-footer"><div class="container">
  <div class="footer-grid">
    <div><h4>Contact Details</h4><p>hello@brightmoor-counsel.com<br>Office 4, Harlow Court House<br>Riverside Lane<br>Northbridge NB4 2QT<br>Tel: 01632 960 418</p></div>
    <div><h4>Nav</h4><ul><li>Home</li><li>What We Do</li><li>How We Do It</li><li>Who Are We</li><li>Clients</li></ul></div>
    <div><h4>Follow Us</h4><div class="social"><span></span><span></span><span></span><span></span></div></div>
    <div><h4>Product</h4><p>Our team helps firms plan, build and run trading systems with clear advice and proven delivery.</p></div>
    <div><h4>Link</h4><ul><li>Case Studies</li><li>Our Clients</li><li>Partners</li><li>Downloads</li><li>Privacy Policy</li></ul></div>
  </div>
</div></footer>
<div class="copyright">Copyright © 2017 Brightmoor Counsel. All rights reserved.</div>
</body>
</html>
```